GJ & DW Fencing Pty Ltd

We already have an existing logo created by Pixel Harbour however we have restructured to a company. We would like someone to add Pty Ltd to our business name please.

Colors

Designer to choose only greyscale colors for use in the design.

```html
<!DOCTYPE html>
<html lang="en">
<head>
<meta charset="utf-8">
<title>GJ &amp; DW Fencing Pty Ltd – Business Card</title>
<link rel="stylesheet" href="https://fonts.googleapis.com/css2?family=Lato:wght@400;700;900&display=swap">
<style>
  :root {
    --page-bg: #e4e4e4;
    --card-bg: #ffffff;
    --ink: #111111;
    --ink-mid: #1d1d1d;
    --on-ink: #ffffff;
    --edge-line: #1c1c1c;
  }
  * { box-sizing: border-box; margin: 0; padding: 0; }
  html, body {
    width: 1200px;
    height: 900px;
    overflow: hidden;
    background: var(--page-bg);
    font-family: "Lato", Arial, sans-serif;
  }
  .business-card {
    position: absolute;
    left: 120px;
    top: 155px;
    width: 960px;
    height: 591px;
    background: var(--card-bg);
    overflow: hidden;
    box-shadow: 0 10px 30px rgba(0,0,0,0.18);
  }
  .illustration-panel {
    position: absolute;
    left: 0;
    top: 0;
    width: 527px;
    height: 591px;
    background: linear-gradient(180deg, var(--ink-mid) 0%, var(--ink) 100%);
  }
  .contact-item {
    position: absolute;
    left: 40px;
    display: flex;
    align-items: flex-start;
    gap: 12px;
    color: var(--on-ink);
    font-size: 26px;
    line-height: 35px;
  }
  .contact-item.address { top: 240px; }
  .contact-item.phone { top: 368px; }
  .contact-item.email { top: 414px; }
  .contact-icon {
    flex: none;
    width: 38px;
    height: 38px;
  }
  .company-name {
    position: absolute;
    left: 520px;
    top: 392px;
    width: 380px;
    color: var(--ink);
    font-weight: 900;
    text-align: center;
    line-height: 1;
  }
  .company-name .name-main { display: block; font-size: 64px; letter-spacing: 1px; }
  .company-name .name-sub { display: block; margin-top: 10px; font-size: 29px; letter-spacing: 3px; }
  .edge-line {
    position: absolute;
    left: 332px;
    right: 0;
    bottom: 0;
    height: 8px;
    background: var(--edge-line);
  }
</style>
</head>
<body>
  <main class="business-card">
    <div class="illustration-panel" role="img" aria-label="Large black sheep illustration standing on the left of the card"></div>

    <div class="contact-item address">
      <svg class="contact-icon" viewBox="0 0 40 40" aria-hidden="true">
        <circle cx="20" cy="20" r="20" fill="var(--on-ink)"/>
        <path fill="var(--ink)" d="M20 8a8 8 0 0 0-8 8c0 6 8 15 8 15s8-9 8-15a8 8 0 0 0-8-8zm0 11a3 3 0 1 1 0-6 3 3 0 0 1 0 6z"/>
      </svg>
      <span>PO Box 418<br>Redgum WA 6523</span>
    </div>
    <div class="contact-item phone">
      <svg class="contact-icon" viewBox="0 0 40 40" aria-hidden="true">
        <circle cx="20" cy="20" r="20" fill="var(--on-ink)"/>
        <path fill="var(--ink)" d="M11 16c0-3 4-5 9-5s9 2 9 5v2h-5v-2h-8v2h-5zM13 20h14l2 9H11z"/>
        <circle cx="20" cy="24" r="2.5" fill="var(--on-ink)"/>
      </svg>
      <span>044 7125590 (DAN)</span>
    </div>
    <div class="contact-item email">
      <svg class="contact-icon" viewBox="0 0 40 40" aria-hidden="true">
        <circle cx="20" cy="20" r="20" fill="var(--on-ink)"/>
        <rect x="10" y="13" width="20" height="14" fill="var(--ink)"/>
        <path d="M10 13l10 8 10-8" fill="none" stroke="var(--on-ink)" stroke-width="1.6"/>
      </svg>
      <span>gjdwfencing@postmail.com</span>
    </div>

    <div class="company-name">
      <span class="name-main">GJ &amp; DW</span>
      <span class="name-sub">FENCING PTY LTD</span>
    </div>

    <div class="edge-line"></div>
  </main>
</body>
</html>
```